Summit Builders Web Site / Business Cards

Construction Company that specializes in Water and Fire Damage, Residential ReModels, Landscaping and Building ADU (Accessory Dwelling Unit)

Growing and changing families often need additional space, and a remodeling project can often provide that. Adding a new area, or repurposing an existing one can satisfy this requirement.

Other times, homeowners want to update the look in their kitchen or bathroom with more than just a change of cabinetry or vanity doors and drawers. Whatever your needs are, Summit Builders has skilled workers who are bonded and insured, and ready to make your dreams and visions a reality.

Target Market(s)

Home Owners

Industry/Entity Type

Construction Company

Contact Information for Business Card

Center Logo with our information on the corners

Back side to be Logo Only
Contact Info
CSLB License # 2418596
info@summitbuildersca.example
www.summitbuildersca.example

Coding

Coded - Design and coding required

Number of Pages Required

5+ page

Font styles to use
Serif
Sans Serif

Requirements
Must have
• Using our Logo Colors
Home
About Us
Services
Projects / Portfolio
Contact Us
Nice to have
• Colors matching our Logo
Should not have
• Black because it doesnt match our logo

```html
<!DOCTYPE html>
<html lang="en">
<head>
<meta charset="utf-8">
<title>Summit Builders – Business Cards</title>
<link href="https://fonts.googleapis.com/css2?family=Montserrat:wght@500;700&display=swap" rel="stylesheet">
<style>
  :root {
    --brand-orange: #ff6a00;
    --brand-orange-deep: #f25a05;
    --paper: #ffffff;
    --ink: #161616;
    --stage: #ececec;
  }
  * { box-sizing: border-box; margin: 0; padding: 0; }
  html, body {
    width: 1200px; height: 800px; overflow: hidden;
    background: var(--stage);
    font-family: "Montserrat", sans-serif;
  }
  .sheet {
    width: 1200px; height: 800px;
    display: flex; align-items: center; justify-content: center; gap: 48px;
  }
  .card {
    width: 504px; height: 288px;
    position: relative; overflow: hidden;
    box-shadow: 0 10px 30px rgba(0,0,0,.12);
  }
  /* Front: logo only */
  .card--front {
    background: linear-gradient(135deg, var(--brand-orange-deep), var(--brand-orange));
    display: flex; align-items: center; justify-content: center;
  }
  .brand {
    display: flex; align-items: center; gap: 12px;
    font-weight: 700; font-size: 34px; letter-spacing: 1px;
    text-transform: uppercase;
  }
  .brand__mark { width: 22px; height: 22px; }
  .card--front .brand { color: var(--paper); }
  .card--front .brand__mark { background: var(--paper); }

  /* Back: logo + contact */
  .card--back { background: var(--paper); }
  .card--back .band {
    position: absolute; left: 0; right: 0; bottom: 0; height: 58%;
    background: linear-gradient(135deg, var(--brand-orange-deep), var(--brand-orange));
  }
  .card--back .brand {
    position: absolute; right: 40px; top: 62px;
    color: var(--ink); font-size: 28px;
  }
  .card--back .brand__mark { background: var(--brand-orange); }
  .contact {
    position: absolute; left: 32px; top: 140px;
    list-style: none; color: var(--paper);
    font-weight: 500; font-size: 15px; line-height: 1;
  }
  .contact li { display: flex; align-items: center; gap: 10px; margin-bottom: 14px; }
  .contact svg { width: 18px; height: 18px; flex: none; }
  .contact .license { padding-left: 28px; }
</style>
</head>
<body>
<main class="sheet">
  <section class="card card--front" aria-label="Business card front">
    <div class="brand"><span class="brand__mark"></span>Summit Builders</div>
  </section>

  <section class="card card--back" aria-label="Business card back">
    <div class="band"></div>
    <div class="brand"><span class="brand__mark"></span>Summit Builders</div>
    <ul class="contact">
      <li class="license">CSLB License # 2418596</li>
      <li>
        <svg viewBox="0 0 20 20" fill="none" stroke="#fff" stroke-width="1.4">
          <rect x="2" y="4.5" width="16" height="11"/>
          <path d="M2 4.5l8 6.5 8-6.5"/>
        </svg>
        info@summitbuildersca.example
      </li>
      <li>
        <svg viewBox="0 0 20 20" fill="none" stroke="#fff" stroke-width="1.4">
          <circle cx="10" cy="10" r="8"/>
          <ellipse cx="10" cy="10" rx="3.5" ry="8"/>
          <path d="M2 10h16M3.5 6h13M3.5 14h13"/>
        </svg>
        www.summitbuildersca.example
      </li>
    </ul>
  </section>
</main>
</body>
</html>
```